Industry automation wholesale website

www.velturo.eu provides solutions for automation, building automation and digital signage.

Our products are rugged, reliable, energy saving and representative.

Scope of pages:
● welcome page
- scope of products
- applications, success stories and news
● category page
- short introduction
- sub categories
- product highlights
● product page
- short introduction
- about 3 to 4 pictures
- technical specifications: materials, dimensions
- price
- related products

Optional:
● contact page
- address
- contact form
● blog
- picture
- text
● logo
● favicon / apple touch icon

Conclusion:
● We need a professionally looking site
● Bright colors (e.g. white, grey, metalic colors, blue)

some pages we like:
http://www.prandek.de/
http://www.morvalix.de/

Target Market(s)

Our target market is the industrial sector
● Target audience: engineering and IT professionals

Industry/Entity Type

Building

Requirements
Must have
• ● only use free available fonts e.g. Lumara Type Library (http://www.lumaratype.com/webfonts)
Should not have
• ● sound
● flash

```html
<!DOCTYPE html>
<html lang="en">
<head>
<meta charset="utf-8">
<title>Velturo – Analog Digital Measurements</title>
<link href="https://fonts.googleapis.com/css2?family=Alegreya+Sans:wght@300;400;500&display=swap" rel="stylesheet">
<style>
:root{
  --blue:#2f77a1;
  --blue-dark:#276a92;
  --blue-text:#3a82a8;
  --card:#dcebef;
  --ink:#2b2b2b;
  --grey-bar:#f3f3f3;
  --rule:#e8e8e8;
  --video:#262626;
  --white:#fff;
}
*{box-sizing:border-box;margin:0;padding:0}
html,body{width:1200px;height:882px;overflow:hidden;background:var(--white)}
body{position:relative;font-family:"Alegreya Sans",sans-serif;color:var(--ink)}
.abs{position:absolute}
.topbar{left:0;top:0;width:1200px;height:25px;background:var(--grey-bar)}
.social{left:178px;top:6px;display:flex;gap:5px}
.social span{width:12px;height:12px;background:var(--blue);display:block;border-radius:2px}
.topnav{top:5px;left:547px;display:flex;gap:12px;font-size:13px;color:var(--ink)}
.topnav .lang{margin-right:15px}
.brand{left:177px;top:50px;display:flex;align-items:center;gap:8px}
.brand-name{font-size:36px;font-weight:400;color:var(--blue);letter-spacing:.5px;line-height:1}
.brand-mark{width:14px;height:14px;background:var(--blue)}
.contact-line{left:863px;display:flex;align-items:center;gap:8px}
.contact-line .value{background:#f3f5f6;color:var(--blue);font-size:11.5px;padding:4px 9px;width:97px;text-align:center}
.mainnav{left:176px;top:115px;display:flex;font-size:13.5px;height:31px;align-items:center}
.mainnav a{color:var(--ink);text-decoration:none;padding:0 20px;line-height:31px}
.mainnav a.active{background:var(--blue);color:var(--white);padding:0 23px}
.navrule{left:176px;top:145px;width:829px;height:6px;background:var(--blue)}
.hero{left:176px;top:151px;width:829px;height:323px;background:#f1f1f1}
.hero-photo{left:176px;top:151px;width:470px;height:323px;background:linear-gradient(90deg,#9ba6ad 0%,#c3cbd0 55%,#e6e8e9 88%,rgba(241,241,241,0) 100%)}
.hero-panel{left:634px;top:158px;width:364px;height:310px;background:var(--white)}
.hero-title{left:630px;top:237px;width:357px;text-align:right;font-size:34px;font-weight:400;color:var(--blue-text);line-height:40px}
.hero-text{left:635px;top:324px;width:348px;text-align:right;font-size:14.5px;line-height:17.3px;font-weight:400}
.card{top:487px;width:200px;height:171px;background:var(--card)}
.card .pic{position:absolute;left:9px;top:6px;width:183px;height:133px;background:linear-gradient(135deg,#5c8fc3,#a9c8e2 60%,#e4eef6)}
.card .label{position:absolute;left:12px;top:146px;font-size:14px;color:var(--blue)}
.slider-track{left:176px;top:671px;width:837px;height:4px;background:var(--rule)}
.slider-thumb{left:266px;top:670px;width:66px;height:7px;background:var(--blue)}
.testimonials{left:191px;top:711px;width:530px}
.testimonials h2{font-size:21px;font-weight:400;margin-bottom:6px}
.testimonials p{font-size:13.5px;line-height:17.6px}
.testimonials .who{margin-top:13px}
.arrows{left:701px;top:716px}
.video{left:780px;top:691px;width:213px;height:147px;background:var(--video);color:var(--white)}
.video .title{position:absolute;left:13px;top:6px;font-size:14px}
.video .frame{position:absolute;left:32px;top:30px;width:150px;height:100px;background:#000}
.video .still{position:absolute;left:32px;top:40px;width:150px;height:78px;background:linear-gradient(180deg,#4a4a4a,#2e2e2e)}
.footer{left:0;top:847px;width:1200px;height:35px;background:var(--blue);display:flex;justify-content:center;align-items:center;gap:12px;font-size:13px;color:var(--white);padding-right:26px}
</style>
</head>
<body>
<div class="abs topbar"></div>
<div class="abs social" aria-label="Social links"><span></span><span></span><span></span><span></span></div>
<nav class="abs topnav"><span class="lang">English</span><span>Community</span><span>Newsletter</span><span>Login</span><span>Online Support</span><span>Contact Us</span><span>Store</span></nav>

<div class="abs brand"><span class="brand-mark"></span><span class="brand-name">velturo</span></div>

<div class="abs contact-line" style="top:42px">
  <svg width="27" height="18" viewBox="0 0 27 18"><rect x="1" y="1" width="25" height="16" fill="none" stroke="var(--blue)" stroke-width="2"/><path d="M1 1 13.5 10 26 1M1 17 10 8M26 17 17 8" fill="none" stroke="var(--blue)" stroke-width="2"/></svg>
  <span class="value">info@velturo.de</span>
</div>
<div class="abs contact-line" style="top:71px">
  <svg width="27" height="24" viewBox="0 0 27 24"><path d="M7 2c-3 1-4 4-3 8 2 6 7 11 12 13 2 1 4 0 5-2l-4-4-3 2c-3-2-5-4-6-7l2-3z" fill="var(--blue)"/></svg>
  <span class="value">+49-211-5550142</span>
</div>

<nav class="abs mainnav"><a class="active">Home</a><a>Products</a><a>Contact</a><a style="padding-left:30px">Shopping Cart</a></nav>
<div class="abs navrule"></div>

<div class="abs hero"></div>
<div class="abs hero-photo" role="img" aria-label="Engineer inspecting a circuit board in a production hall"></div>
<div class="abs hero-panel"></div>
<h1 class="abs hero-title">Expand Your Engineering Horizon</h1>
<p class="abs hero-text">Velturo provides analog digital measurement devices which provide analog inputs/outputs, digital inputs/outputs, and more. They serve as an inexpensive and easy to use interface between computers and the physical world.</p>

<div class="abs card" style="left:176px"><div class="pic" role="img" aria-label="Row of Modbus RTU modules"></div><span class="label">Modbus RTU</span></div>
<div class="abs card" style="left:386px"><div class="pic" role="img" aria-label="Touch panel industry computer" style="background:linear-gradient(135deg,#c9cdd0,#8fb6dc 40%,#5b9ad6 70%,#c9cdd0)"></div><span class="label" style="left:7px">Touch Panel Industry Computer</span></div>
<div class="abs card" style="left:598px"><div class="pic" role="img" aria-label="Row of embedded system modules"></div><span class="label" style="left:7px">Embeded Systems</span></div>
<div class="abs card" style="left:808px"><div class="pic" role="img" aria-label="RS422 / RS485 converter module" style="left:5px;background:radial-gradient(circle at 50% 50%,#6f8fd0 0 22%,#fff 42%)"></div><span class="label">RS422 / RS485 Converter</span></div>

<div class="abs slider-track"></div>
<div class="abs slider-thumb"></div>

<section class="abs testimonials">
  <h2>Testimonials</h2>
  <p>“the velturo is having brilliant staff, they are having their quality control team which plays an important role. best wishes to velturo.”</p>
  <p class="who">- Lena Hartwig, Orvena Systems</p>
</section>
<svg class="abs arrows" width="17" height="14" viewBox="0 0 17 14"><path d="M7 0 0 7 7 14zM10 0l7 7-7 7z" fill="var(--ink)"/></svg>

<div class="abs video">
  <span class="title">Watch Video</span>
  <div class="frame"></div>
  <div class="still" role="img" aria-label="Video still of a speaker"></div>
  <svg style="position:absolute;left:95px;top:68px" width="24" height="24" viewBox="0 0 24 24"><circle cx="12" cy="12" r="10" fill="none" stroke="#fff" stroke-width="2"/><path d="M9.5 7v10l8-5z" fill="#fff"/></svg>
</div>

<footer class="abs footer"><span>Home</span><span>Products</span><span>Shopping</span><span>Community</span><span>Newsletter</span><span>Login</span><span>Online Support</span><span>Contact Us</span><span>Store</span></footer>
</body>
</html>
```